Business Card Design Project

We are not a new company, but renamed to "Vantorin Kitchens" last year. We specialize in modern high-end cabinetry imports. We would like to communicate a sense of quality and cutting edge technology. Ideally the design would incorporate our logo colors, silver, red and preferably a black, matte background. Though we are open to suggestions.
Logo is attached.
Edit: I have attached rough drafts of the previous cards, this way you will have all necessary content that needs to go on the cards.
Updates
Project Deadline Extended
Reason: We have received a lot of great designs, but due to the sheer number we couldn't respond to all. We will extend the deadline for another 7 days to finalize and provide feedback to designers.
Thank you for your hard work!
Industry/Entity Type
Business
Look and feel
Each slider illustrates characteristics of the customer's brand and the style your logo design should communicate.

```html
<!DOCTYPE html>
<html lang="en">
<head>
<meta charset="utf-8">
<title>Vantorin Kitchens – Business Cards</title>
<link rel="stylesheet" href="https://fonts.googleapis.com/css2?family=Arimo:wght@400;700&display=swap">
<style>
  :root {
    --stage: #e8e5e1;
    --label: #2b2b2b;
    --card-light: #2c2c2e;
    --card-dark: #0b0b0c;
    --silver: #b8bcc1;
    --silver-light: #e2e4e6;
    --red: #e3222b;
    --white: #ffffff;
    --address-ink: #2a2a2a;
  }
  * { margin: 0; padding: 0; box-sizing: border-box; }
  html, body { width: 1200px; height: 788px; overflow: hidden; }
  body {
    background: var(--stage);
    font-family: "Arimo", Arial, sans-serif;
    position: relative;
  }
  .sheet-label {
    position: absolute;
    width: 526px;
    text-align: center;
    font-size: 21px;
    color: var(--label);
  }
  .card {
    position: absolute;
    width: 526px;
    height: 300px;
    border-radius: 22px;
    overflow: hidden;
    background: radial-gradient(ellipse at 50% 30%, var(--card-light) 0%, #161617 60%, var(--card-dark) 100%);
    box-shadow: 0 6px 14px rgba(0,0,0,0.35);
    color: var(--white);
  }
  .brand-name {
    position: absolute;
    left: 0; right: 0;
    text-align: center;
    font-weight: 700;
    text-transform: uppercase;
    letter-spacing: 2px;
    color: var(--silver);
  }
  .front .brand-name { top: 94px; font-size: 24px; }
  .back .brand-name { top: 160px; font-size: 30px; }
  .back-alt { background: #070707; }
  .back-alt .brand-name { color: var(--silver-light); }
  .person {
    position: absolute;
    top: 154px; left: 0; right: 0;
    text-align: center;
    font-size: 16px;
  }
  .person .name { font-weight: 700; }
  .person .role { font-size: 15px; }
  .contact-line {
    position: absolute;
    top: 193px; left: 0; right: 0;
    text-align: center;
    font-size: 13.5px;
  }
  .contact-line b { font-weight: 700; }
  .bands { position: absolute; left: 0; top: 0; }
  .address {
    position: absolute;
    left: 20px; top: 240px;
    font-size: 13.5px;
    color: var(--address-ink);
  }
  .email {
    position: absolute;
    right: 34px; top: 257px;
    font-size: 13.5px;
    color: var(--white);
  }
  .texture {
    position: absolute;
    width: 300px; height: 150px;
  }
  .texture-top {
    left: 0; top: 0;
    background: radial-gradient(ellipse at 45% 20%, rgba(120,120,120,0.55) 0%, rgba(40,40,40,0.4) 45%, rgba(7,7,7,0) 75%);
  }
  .texture-bottom {
    right: 0; bottom: 0;
    background: radial-gradient(ellipse at 55% 80%, rgba(120,120,120,0.55) 0%, rgba(40,40,40,0.4) 45%, rgba(7,7,7,0) 75%);
  }
</style>
</head>
<body>

  <div class="sheet-label" style="left:53px; top:22px;">front</div>
  <div class="sheet-label" style="left:620px; top:22px;">front-1</div>
  <div class="sheet-label" style="left:56px; top:406px;">back</div>
  <div class="sheet-label" style="left:624px; top:406px;">Back - 1</div>

  <section class="card front" style="left:53px; top:74px;">
    <div class="brand-name">Vantorin Kitchens</div>
    <div class="person"><span class="name">MAREK DOVAL,</span> <span class="role">President</span></div>
    <div class="contact-line"><b>p</b> : 555.210.4400 &nbsp;|&nbsp; <b>c</b> : 555.210.7731 &nbsp;|&nbsp; <b>f</b> : 555.210.4409</div>
    <svg class="bands" width="526" height="300" viewBox="0 0 526 300">
      <defs>
        <linearGradient id="silverBandA" x1="0" y1="0" x2="1" y2="0">
          <stop offset="0" stop-color="#b9bbbe"/>
          <stop offset="0.7" stop-color="#dadcde"/>
          <stop offset="1" stop-color="#c3c5c8"/>
        </linearGradient>
      </defs>
      <polygon points="0,231 307,231 275,264 0,264" fill="url(#silverBandA)"/>
      <polygon points="268,248 526,248 526,281 242,281" fill="var(--red)"/>
    </svg>
    <div class="address">1280 - 48 Ave., Northgate, AB T0K 2R5</div>
    <div class="email">marek@vantorinkitchens.ca</div>
  </section>

  <section class="card front" style="left:620px; top:74px;">
    <div class="brand-name">Vantorin Kitchens</div>
    <div class="person"><span class="name" style="font-weight:400;">PAVEL DOVAL,</span> <span class="role" style="font-size:13px;">Director</span></div>
    <div class="contact-line"><b>p</b> : 555.210.4400 &nbsp;|&nbsp; <b>c</b> : 555.210.8842 &nbsp;|&nbsp; <b>f</b> : 555.210.4409</div>
    <svg class="bands" width="526" height="300" viewBox="0 0 526 300">
      <defs>
        <linearGradient id="silverBandB" x1="0" y1="0" x2="1" y2="0">
          <stop offset="0" stop-color="#b9bbbe"/>
          <stop offset="0.7" stop-color="#dadcde"/>
          <stop offset="1" stop-color="#c3c5c8"/>
        </linearGradient>
      </defs>
      <polygon points="0,231 307,231 275,264 0,264" fill="url(#silverBandB)"/>
      <polygon points="268,248 526,248 526,281 242,281" fill="var(--red)"/>
    </svg>
    <div class="address">1280 - 48 Ave., Northgate, AB T0K 2R5</div>
    <div class="email">pavel@vantorinkitchens.ca</div>
  </section>

  <section class="card back" style="left:56px; top:446px;">
    <div class="brand-name">Vantorin Kitchens</div>
  </section>

  <section class="card back back-alt" style="left:624px; top:446px;">
    <div class="texture texture-top" role="img" aria-label="Perforated metal texture fading in from the top left corner"></div>
    <div class="texture texture-bottom" role="img" aria-label="Perforated metal texture fading in from the bottom right corner"></div>
    <div class="brand-name">Vantorin Kitchens</div>
  </section>

</body>
</html>
```